Web Developer Needs a Business Card Design

I need a personal business card design that represents me as a web developer for potential employers. I would like the background to be a dark color on the front for contrast with my logo and name. The back will have all my information along with a smaller version of the logo. I want something with a modern look and feel, not too conservative. This will be used for potential employers and freelance work.

Industry/Entity Type

Business

Contact Information for Business Card

Front should have my logo and name. The back should have all my personal information which would include: name: Tom Varulek, phone: 570-614-3098, email: tomvarulek@quillbox.net, website url: www.tomvarulek.net, logo, web developer.

Font styles to use
Sans Serif

Requirements
Must have
• Must include my logo. The color palette base color will be the logo color.

```html
<!DOCTYPE html>
<html lang="en">
<head>
<meta charset="utf-8">
<title>Tom Varulek – Business Card</title>
<link rel="stylesheet" href="https://fonts.googleapis.com/css2?family=Roboto:wght@300;400&display=swap">
<style>
  :root {
    --bg: #e9e7e3;
    --card-black: #0c0c0c;
    --teal: #8fd6c6;
    --teal-deep: #6cbfae;
    --white: #f4f4f4;
    --grey-line: #8a8a8a;
  }
  * { box-sizing: border-box; margin: 0; padding: 0; }
  html, body {
    width: 1200px; height: 892px; overflow: hidden;
    background: var(--bg);
    font-family: "Roboto", sans-serif;
  }
  .stage {
    width: 1200px; height: 892px;
    display: flex; align-items: center; justify-content: center; gap: 48px;
  }
  .card {
    position: relative;
    width: 540px; height: 309px;
    border-radius: 22px;
    overflow: hidden;
    background: var(--card-black);
    box-shadow: 0 10px 30px rgba(0,0,0,.22);
  }
  .card-shapes { position: absolute; inset: 0; }

  /* back side: contact details */
  .back .mark-ring {
    position: absolute; left: 78px; top: 36px;
    width: 116px; height: 116px; border-radius: 50%;
    border: 9px solid var(--teal);
  }
  .back .identity {
    position: absolute; left: 60px; top: 168px; text-align: right; width: 196px;
  }
  .identity .name {
    color: var(--teal); font-weight: 300; font-size: 27px; letter-spacing: .3px;
  }
  .identity .role {
    color: var(--white); font-weight: 300; font-size: 14px; margin-top: 2px;
  }
  .divider {
    position: absolute; left: 276px; top: 118px; width: 1px; height: 118px;
    background: var(--grey-line);
  }
  .contacts {
    position: absolute; left: 296px; top: 104px; list-style: none;
  }
  .contacts li {
    display: flex; align-items: center; gap: 9px;
    color: var(--white); font-weight: 300; font-size: 15px; line-height: 1; margin-bottom: 13px;
  }
  .contacts svg { width: 13px; height: 13px; flex: none; }

  /* front side: mark and name */
  .front .mark-ring {
    position: absolute; left: -38px; top: 62px;
    width: 186px; height: 186px; border-radius: 50%;
    border: 14px solid var(--teal);
  }
  .front .headline {
    position: absolute; left: 176px; top: 132px;
    color: var(--white); font-weight: 400; font-size: 38px; letter-spacing: 2px;
    text-transform: uppercase;
  }
</style>
</head>
<body>
<main class="stage">

  <section class="card back" aria-label="Card back with contact details">
    <svg class="card-shapes" viewBox="0 0 540 309" aria-hidden="true">
      <path d="M300 0 Q470 30 540 150 L540 0 Z" fill="var(--white)"/>
      <path d="M322 0 Q480 34 540 128 L540 0 Z" fill="var(--teal)"/>
      <path d="M0 186 Q120 250 300 309 L0 309 Z" fill="var(--white)"/>
      <path d="M0 206 Q110 262 262 309 L0 309 Z" fill="var(--teal)"/>
    </svg>
    <div class="mark-ring"></div>
    <div class="identity">
      <div class="name">Tom Varulek</div>
      <div class="role">web developer</div>
    </div>
    <div class="divider"></div>
    <ul class="contacts">
      <li>
        <svg viewBox="0 0 13 13"><rect width="13" height="13" rx="2" fill="var(--teal)"/><path d="M4 3 L5.5 3 L6 5 L5 5.8 Q6 7.6 7.2 8 L8 7 L10 7.5 L10 9 Q6 10 3.5 5 Z" fill="var(--card-black)"/></svg>
        570-614-3098
      </li>
      <li>
        <svg viewBox="0 0 13 13"><rect width="13" height="13" rx="2" fill="var(--teal)"/><rect x="3" y="4" width="7" height="5" fill="none" stroke="var(--card-black)" stroke-width="1"/><path d="M3 4 L6.5 7 L10 4" fill="none" stroke="var(--card-black)" stroke-width="1"/></svg>
        tomvarulek@quillbox.net
      </li>
      <li>
        <svg viewBox="0 0 13 13"><rect width="13" height="13" rx="2" fill="var(--teal)"/><circle cx="6.5" cy="6.5" r="3.5" fill="none" stroke="var(--card-black)" stroke-width="1"/><path d="M3 6.5 H10 M6.5 3 V10" stroke="var(--card-black)" stroke-width=".8"/></svg>
        www.tomvarulek.net
      </li>
    </ul>
  </section>

  <section class="card front" aria-label="Card front with name">
    <svg class="card-shapes" viewBox="0 0 540 309" aria-hidden="true">
      <rect x="0" y="0" width="540" height="40" fill="var(--teal)"/>
      <rect x="0" y="40" width="540" height="10" fill="var(--white)"/>
      <rect x="0" y="259" width="540" height="10" fill="var(--white)"/>
      <rect x="0" y="269" width="540" height="40" fill="var(--teal)"/>
    </svg>
    <div class="mark-ring"></div>
    <h1 class="headline">Tom Varulek</h1>
  </section>

</main>
</body>
</html>
```